Zielgruppe
Wir verkaufen in unserem Onlineshop alles zum Thema Wohnen mit dem Schwerpunkt Möbel. Die Hauptzielgruppe ist zwischen 25 und 45 Jahren.
Aufgabenstellung
Wir bevorzugen ein modernes, flaches und aufgeräumtes Design ähnlich wie kranu.de / pelvix31.de mit dem Fokus auf Preisaggressivität und Rabatte.
- Das Grundlayout muss so bleiben, wie es aktuell ist. Natürlich dürfen einzelne Elemente verschoben / versetzt werden.
- Im Header sollte Platz für eine kleine Werbefläche sein (ähnlich wie der konfigurierbare Kleiderschrank).
- Der Shop basiert auf Tervano 1.9.
- Die Rabatte in den Produktdetailseiten müssen genauso aufgebaut sein
- Die Suche sollte in den Header platziert werden und nicht im Menü
- Ein SSL Logo soll im Header platziert weden
- Die Vorteile (Kostenloser Versand, Sicher einkaufen, Kauf auf Rechnung) sollen im Header erscheinen
- Das Design sollte responsive sein
Es wird nur das reine Design ohne Programmierung benötigt.

```html
<!DOCTYPE html>
<html lang="de">
<head>
<meta charset="utf-8">
<title>moebelwelt7 – Schlafzimmer</title>
<link href="https://fonts.googleapis.com/css2?family=Ubuntu:wght@300;400;500;700&family=Open+Sans:wght@400;600;700&display=swap" rel="stylesheet">
<style>
:root{
  --green:#78b22e;
  --teal:#38a8c0;
  --ink:#222;
  --muted:#777;
  --line:#e3e3e3;
  --bar:#f4f4f4;
  --white:#fff;
  --red:#e3262b;
}
*{box-sizing:border-box;margin:0;padding:0}
html,body{width:954px;height:1200px;overflow:hidden;background:var(--white)}
body{position:relative;font-family:"Open Sans",sans-serif;color:var(--ink)}
.abs{position:absolute}
.ub{font-family:"Ubuntu",sans-serif}

.topbar{left:0;top:0;width:954px;height:30px;background:var(--bar)}
.top-phone{left:135px;top:5px;font:500 16px "Ubuntu",sans-serif;color:#555;display:flex;align-items:center;gap:5px}
.top-hours{left:288px;top:7px;font-size:5px;line-height:7px;color:#555}
.promo-badge{left:383px;top:-6px;width:36px;height:36px;border-radius:50%;background:var(--teal);color:#fff;font:700 16px "Ubuntu",sans-serif;display:flex;align-items:center;justify-content:center}
.promo-title{left:423px;top:3px;font:500 12px "Ubuntu",sans-serif;color:var(--teal)}
.promo-sub{left:423px;top:17px;font-size:6px;color:#333}
.top-voucher{left:669px;top:10px;font-size:7px;color:#444}
.top-contact{left:793px;top:10px;font-size:7px;color:#444}

.logo{left:134px;top:50px;font:700 26px "Ubuntu",sans-serif;color:var(--green);letter-spacing:-0.5px}
.search{left:321px;top:52px;width:360px;height:31px;border:1px solid var(--line);border-radius:2px;font:300 12px "Ubuntu",sans-serif;color:#666;padding:8px 11px}
.search svg{position:absolute;right:10px;top:9px}
.seal{top:51px;width:32px;height:32px;border-radius:50%;background:#8d8d8d;border:3px solid #cfcfcf}
.seal-box{left:798px;top:50px;width:22px;height:33px;background:#bdbdbd;border-radius:2px}

.nav{left:0;top:110px;width:954px;height:46px;border-top:1px solid var(--line);border-bottom:1px solid var(--line)}
.nav-items{left:126px;top:110px;width:531px;height:46px;border-left:1px solid var(--line);display:flex;align-items:center;gap:0;font-size:9.3px;letter-spacing:.2px}
.nav-items span{position:absolute;top:18px}
.nav-cell{top:110px;width:57px;height:46px;border-left:1px solid var(--line);display:flex;align-items:center;justify-content:center}
.cart-count{left:805px;top:114px;width:18px;height:18px;border-radius:50%;background:var(--teal);color:#fff;font:700 11px "Ubuntu",sans-serif;display:flex;align-items:center;justify-content:center}

.crumbs{left:134px;top:163px;font-size:8px;color:#aaa}
.crumb-line{left:126px;top:181px;width:706px;height:1px;background:var(--line)}
.title{left:134px;top:196px;width:660px;font:400 15.5px/22px "Ubuntu",sans-serif}

.hero{left:134px;top:265px;width:493px;height:331px;background:linear-gradient(135deg,#e8e3da 0%,#d6ccbd 35%,#b7c59b 60%,#6f6a60 100%)}
.sale-circle{left:578px;top:250px;width:68px;height:68px;border-radius:50%;background:var(--teal);color:#fff;font:500 22px "Ubuntu",sans-serif;display:flex;align-items:center;justify-content:center}
.thumb{top:605px;width:115px;height:75px;background:linear-gradient(135deg,#e5e0d7,#b8ab93)}
.thumb.active{border:2px solid var(--teal)}

.contact{left:134px;top:704px;width:493px;height:97px;border:1px solid var(--line);border-radius:2px}
.contact-q{left:160px;top:726px;font-size:9.5px}
.contact-phone{left:158px;top:748px;font:500 15px "Ubuntu",sans-serif;color:var(--green);display:flex;gap:6px;align-items:center}
.contact-hours{left:185px;top:767px;font-size:5.5px}
.field{left:332px;width:175px;border:1px solid #ddd;border-radius:2px;font-size:6.5px;color:#bbb;padding:3px 8px}
.send{left:332px;top:772px;width:107px;height:18px;background:var(--teal);color:#fff;font-size:6.5px;font-weight:700;display:flex;align-items:center;justify-content:center;border-radius:2px}
.agent{left:512px;top:700px;width:108px;height:101px;background:linear-gradient(180deg,#f3ece6,#e6e9ef)}

.old-price{left:657px;top:267px;font:400 14.5px "Ubuntu",sans-serif;text-decoration:line-through}
.disc{left:657px;width:162px;font-size:7.2px;display:flex;justify-content:space-between;align-items:center}
.disc b{font:400 9px "Ubuntu",sans-serif;text-decoration:line-through}
.rline{left:657px;width:162px;height:1px;background:var(--line)}
.acc-title{left:658px;top:344px;font:300 11px "Ubuntu",sans-serif;color:#555}
.acc-plus{left:804px;top:343px;width:15px;height:15px;border:1px solid #ddd;font-size:9px;color:var(--teal);display:flex;align-items:center;justify-content:center}
.acc-img{left:658px;top:369px;width:41px;height:41px;background:linear-gradient(180deg,#f0f0f0,#7d5a45 50%,#f0f0f0)}
.acc-name{left:709px;top:370px;font-size:7px;line-height:12px}
.acc-price{left:709px;top:398px;font:400 9.5px "Ubuntu",sans-serif;color:var(--teal)}
.acc-x{left:808px;top:399px;color:#bbb;font-size:11px}
.price{left:656px;top:433px;font:400 25px "Ubuntu",sans-serif;color:var(--teal)}
.rate{left:657px;top:467px;font-size:8.2px}
.rate em{font-style:normal;color:var(--teal)}
.qty-label{left:657px;top:513px;font-size:8.5px}
.qty{left:716px;top:504px;width:30px;height:30px;border:1px solid #ddd;font:400 13px "Ubuntu",sans-serif;display:flex;align-items:center;justify-content:center}
.qty-step{left:749px;top:504px;width:15px;height:30px;border:1px solid #ddd;font-size:10px;color:#999;display:flex;flex-direction:column;align-items:center;justify-content:space-around;line-height:1}
.cart-btn{left:657px;top:547px;width:162px;height:36px;background:var(--green);color:#fff;font:500 11px "Ubuntu",sans-serif;letter-spacing:.5px;display:flex;align-items:center;justify-content:center;gap:8px;border-radius:2px}
.save-btn{left:657px;top:590px;width:162px;height:24px;border:1px solid #ddd;font-size:8px;font-weight:700;color:#666;display:flex;align-items:center;justify-content:center;border-radius:2px}
.save-btn svg{position:absolute;left:17px}
.feat{left:657px;font-size:8.5px;display:flex;align-items:center;gap:13px}
.feat .ico{width:18px;display:flex;justify-content:center}
.social{left:660px;top:772px;display:flex;gap:3px}
.social span{background:#4267b2;color:#fff;font-size:8px;font-weight:700;padding:3px 5px;border-radius:2px}

.sec-title{left:134px;font:300 20px "Ubuntu",sans-serif;letter-spacing:.3px}
.arrow-btn{top:846px;width:36px;height:36px;border:1px solid #ddd;border-radius:50%;display:flex;align-items:center;justify-content:center}
.card-img{top:897px;width:162px;height:111px;background:radial-gradient(circle,#fafafa,#eee)}
.card-name{top:1021px;width:150px;font:300 11px/14px "Ubuntu",sans-serif}
.card-price{top:1063px;font:400 15.5px "Ubuntu",sans-serif}
.card-qty{top:1062px;width:27px;height:25px;border:1px solid #ddd;font-size:10px;display:flex;align-items:center;justify-content:center}
.card-step{top:1062px;width:12px;height:25px;border:1px solid #ddd;color:#999;font-size:8px;display:flex;flex-direction:column;align-items:center;justify-content:space-around;line-height:1}
.badge-17{left:479px;top:892px;width:42px;height:42px;border-radius:50%;background:var(--teal);color:#fff;font:500 13px "Ubuntu",sans-serif;display:flex;align-items:center;justify-content:center}
.intro{left:134px;top:1170px;font:400 13px "Ubuntu",sans-serif}
.dims{left:657px;top:1135px;width:162px;height:70px;background:#f4f4f4;padding:10px 14px}
.dims h4{font:400 8.5px "Ubuntu",sans-serif;color:var(--teal);margin-bottom:5px}
.dims li{font-size:6.8px;line-height:12px;margin-left:10px;color:#333}
.dims li::marker{color:var(--teal)}
</style>
</head>
<body>

<div class="abs topbar"></div>
<div class="abs top-phone">
  <svg width="14" height="14" viewBox="0 0 20 20"><circle cx="10" cy="10" r="9" fill="none" stroke="var(--green)" stroke-width="1.5"/><path d="M6 5c1-1 2 0 2.5 1.5s-1 1.5-.5 2.5 2 2.5 3 3 1-1 2.3-.5 2 1.5 1 2.5-3 .5-5-1.5S4.5 6.5 6 5z" fill="var(--green)"/></svg>
  0571 / 24 61 73 50
</div>
<div class="abs top-hours">Mo-Fr 9-21 Uhr<br>Sa 10-15 Uhr</div>
<div class="abs promo-badge">10%</div>
<div class="abs promo-title">EINFÜHRUNGSRABATTE ›</div>
<div class="abs promo-sub">Kleiderschrank jetzt auch selbst Zusammenstellen</div>
<div class="abs top-voucher">5 € Gutschein jetzt sichern! ⌄</div>
<div class="abs top-contact">Kontakt</div>

<div class="abs logo">moebelwelt7</div>
<div class="abs search">Suche...
  <svg width="12" height="12" viewBox="0 0 12 12"><circle cx="5" cy="5" r="4" fill="none" stroke="#777" stroke-width="1"/><path d="M8 8l3.5 3.5" stroke="#777"/></svg>
</div>
<div class="abs seal" style="left:704px"></div>
<div class="abs seal" style="left:751px"></div>
<div class="abs seal-box"></div>

<div class="abs nav"></div>
<nav class="abs nav-items">
  <span style="left:14px">WOHNEN</span>
  <span style="left:76px">SCHLAFEN</span>
  <span style="left:145px">KINDER-BABY</span>
  <span style="left:225px">ESSEN</span>
  <span style="left:275px">KUCHE</span>
  <span style="left:328px">BIS 60% RABATT</span>
  <span style="left:421px">SONSTIGES</span>
  <span style="left:493px;color:var(--teal);font-weight:700">SALE</span>
</nav>
<div class="abs nav-cell" style="left:657px"><svg width="20" height="20" viewBox="0 0 20 20" fill="none" stroke="#444" stroke-width="1"><circle cx="10" cy="7" r="4"/><path d="M2 19c0-4 3-6 8-6s8 2 8 6z"/></svg></div>
<div class="abs nav-cell" style="left:714px"><svg width="20" height="20" viewBox="0 0 20 20" fill="none" stroke="#444" stroke-width="1"><path d="M2 2h7l9 9-7 7-9-9z"/><circle cx="6" cy="6" r="1.3"/></svg></div>
<div class="abs nav-cell" style="left:771px;width:58px;border-right:1px solid var(--line)"><svg width="26" height="22" viewBox="0 0 26 22" fill="none" stroke="#444" stroke-width="1"><path d="M1 2h4l3 12h14l3-9H7"/><circle cx="10" cy="19" r="1.6"/><circle cx="19" cy="19" r="1.6"/></svg></div>
<div class="abs cart-count">3</div>

<div class="abs crumbs">Startseite &nbsp;→&nbsp; Schlafen &nbsp;→&nbsp; Schlafzimmer</div>
<div class="abs crumb-line"></div>
<h1 class="abs title">Schlafzimmer in Eiche sägerau-Nb/Glas weiß, Kleiderschrank (B: ca. 300 cm), Futonbett (Liegefläche: ca. 180 x 200 cm), 2 Nachtschränken (B: ca. 60 cm)</h1>

<div class="abs hero" role="img" aria-label="Produktfoto: Schlafzimmer mit weißem Kleiderschrank, Futonbett und Nachtschränken vor großem Sprossenfenster"></div>
<div class="abs sale-circle">-25%</div>
<div class="abs thumb active" style="left:134px" role="img" aria-label="Vorschaubild Schlafzimmer"></div>
<div class="abs thumb" style="left:260px" role="img" aria-label="Vorschaubild Bett und Nachtschrank"></div>
<div class="abs thumb" style="left:386px" role="img" aria-label="Vorschaubild Kleiderschrank"></div>
<div class="abs thumb" style="left:512px" role="img" aria-label="Vorschaubild Schlafzimmer Gesamtansicht"></div>

<div class="abs contact"></div>
<div class="abs contact-q">Sie haben Fragen?</div>
<div class="abs contact-phone">
  <svg width="20" height="20" viewBox="0 0 20 20"><circle cx="10" cy="10" r="9" fill="none" stroke="var(--green)" stroke-width="1.3"/><path d="M6 5c1-1 2 0 2.5 1.5s-1 1.5-.5 2.5 2 2.5 3 3 1-1 2.3-.5 2 1.5 1 2.5-3 .5-5-1.5S4.5 6.5 6 5z" fill="var(--green)"/></svg>
  0571 / 24 61 73 50
</div>
<div class="abs contact-hours">Mo-Fr 9-21 Uhr &nbsp; Sa 10-15 Uhr</div>
<div class="abs field" style="top:714px;height:19px">Ihre E-mail adresse</div>
<div class="abs field" style="top:736px;height:33px">Ihre Nachricht</div>
<div class="abs send">NACHRICHT VERSENDEN</div>
<div class="abs agent" role="img" aria-label="Kundenberaterin mit Headset"></div>

<div class="abs old-price">2.799,00 €<sup style="font-size:8px">**</sup></div>
<div class="abs disc" style="top:293px"><span><span style="color:var(--green)">✓</span>&nbsp; Online-Rabatt von uns</span><b>-650,00 €</b></div>
<div class="abs disc" style="top:307px"><span><span style="color:var(--green)">✓</span>&nbsp; Geburtstags-Rabatt</span><b>-150,43 €*</b></div>
<div class="abs rline" style="top:330px"></div>
<div class="abs acc-title">ZUBEHÖR AUSWÄHLEN</div>
<div class="abs acc-plus">+</div>
<div class="abs acc-img" role="img" aria-label="Schubkastenkommode"></div>
<div class="abs acc-name">Schubkastenkommode in Eiche<br>sägerau-Nachb./ Glas weiß</div>
<div class="abs acc-price">+259,00 €<sup style="font-size:5px">*</sup></div>
<div class="abs acc-x">×</div>
<div class="abs rline" style="top:426px"></div>
<div class="abs price">1.998,57 €<sup style="font-size:12px">*</sup></div>
<div class="abs rate">nur <em>36,50 €</em> / 72 Monate ›</div>
<div class="abs rline" style="top:490px"></div>
<div class="abs qty-label">Stück:</div>
<div class="abs qty">1</div>
<div class="abs qty-step"><span>+</span><span>−</span></div>
<div class="abs cart-btn">
  <svg width="22" height="18" viewBox="0 0 26 22" fill="none" stroke="#fff" stroke-width="1.2"><path d="M1 2h4l3 12h14l3-9H7"/><circle cx="10" cy="19" r="1.6"/><circle cx="19" cy="19" r="1.6"/></svg>
  IN DEN WARENKORB
</div>
<div class="abs save-btn">
  <svg width="14" height="14" viewBox="0 0 20 20" fill="none" stroke="#888" stroke-width="1.2"><path d="M2 2h7l9 9-7 7-9-9z"/><circle cx="6" cy="6" r="1.3"/></svg>
  ARTIKEL MERKEN
</div>

<div class="abs feat" style="top:640px;font-weight:700"><span class="ico"><svg width="18" height="13" viewBox="0 0 18 13" fill="none" stroke="#555"><rect x="6" y="1" width="11" height="8"/><path d="M6 4H3L1 7v3h5"/><circle cx="4" cy="11" r="1.4"/><circle cx="13" cy="11" r="1.4"/></svg></span>Kostenlose Lieferung</div>
<div class="abs feat" style="top:670px"><span class="ico"><svg width="16" height="15" viewBox="0 0 16 15" fill="none" stroke="#555"><rect x="1" y="2" width="14" height="12"/><path d="M1 5h14M5 5v9M9 5v9M1 9h14"/></svg></span>Lieferzeit: 5 bis 6 Wochen</div>
<div class="abs feat" style="top:698px"><span class="ico"><svg width="16" height="11" viewBox="0 0 16 11"><rect width="16" height="11" fill="var(--red)"/><rect y="3.7" width="16" height="3.6" fill="#fff"/></svg></span>Wir liefern nach Österreich &nbsp;›</div>
<div class="abs feat" style="top:725px"><span class="ico"><svg width="16" height="11" viewBox="0 0 16 11"><rect width="16" height="11" fill="var(--red)"/><path d="M7 2.5h2v2h2v2H9v2H7v-2H5v-2h2z" fill="#fff"/></svg></span>Wir liefern nach Schweiz &nbsp;›</div>
<div class="abs rline" style="top:755px"></div>
<div class="abs social"><span>Like 109</span><span>Share</span></div>

<h2 class="abs sec-title" style="top:848px">PASSENDES ZUBEHÖR</h2>
<div class="abs arrow-btn" style="left:738px"><svg width="12" height="10" viewBox="0 0 12 10" fill="none" stroke="#555" stroke-width="1.2"><path d="M11 5H1M5 1L1 5l4 4"/></svg></div>
<div class="abs arrow-btn" style="left:785px"><svg width="12" height="10" viewBox="0 0 12 10" fill="none" stroke="#555" stroke-width="1.2"><path d="M1 5h10M7 1l4 4-4 4"/></svg></div>

<div class="abs card-img" style="left:136px" role="img" aria-label="Einlegeböden"></div>
<div class="abs card-img" style="left:311px" role="img" aria-label="Kleiderstange"></div>
<div class="abs card-img" style="left:485px" role="img" aria-label="Schwarze Kommode"></div>
<div class="abs card-img" style="left:658px;background:radial-gradient(circle,#6b4a38 0 40%,#f0f0f0 60%)" role="img" aria-label="Sideboard in Nussbaum"></div>
<div class="abs badge-17">-17%</div>

<div class="abs card-name" style="left:146px">Einlegeboden 2er-Satz, Maße: B/H/T/ ca. 110/2/50</div>
<div class="abs card-name" style="left:320px">Boxspringbett schwarz, Feinstrukturstoff</div>
<div class="abs card-name" style="left:494px">Boxspringbett schwarz, Feinstrukturstoff</div>
<div class="abs card-name" style="left:668px">Boxspringbett schwarz, Feinstrukturstoff</div>

<div class="abs card-price" style="left:146px">54,95 €</div>
<div class="abs card-price" style="left:320px">119,95 €</div>
<div class="abs card-price" style="left:494px;color:var(--teal)">79,95 €</div>
<div class="abs card-price" style="left:668px">159,95 €</div>

<div class="abs card-qty" style="left:250px">1</div><div class="abs card-step" style="left:279px"><span>+</span><span>−</span></div>
<div class="abs card-qty" style="left:424px">1</div><div class="abs card-step" style="left:453px"><span>+</span><span>−</span></div>
<div class="abs card-qty" style="left:598px">1</div><div class="abs card-step" style="left:627px"><span>+</span><span>−</span></div>
<div class="abs card-qty" style="left:772px">1</div><div class="abs card-step" style="left:801px"><span>+</span><span>−</span></div>

<h2 class="abs sec-title" style="top:1132px">PASSENDES ZUBEHÖR</h2>
<p class="abs intro">Freuen Sie sich auf ein wirkungsvolles Schlafzimmer</p>
<div class="abs dims">
  <h4>Abmessungen im Detail (B/H/T ca.)</h4>
  <ul>
    <li>Schwebetürenschrank:<br>225/210/65 cm</li>
    <li>Bett:188/38/208 cm</li>
  </ul>
</div>

</body>
</html>
```